Business Card for Polygraph business in Africa

Business Card . Polygraph Examiner based in Tanzania, East Africa.
Business Card will be used to disseminate contact information to potential clients.
It should convey that I am a professional specifically in the polygraph field and perform my work with integrity.

I have attached the business card that I'm currently using, which I threw together myself initially. It's not professional enough.

Target Market(s)

Banks, Accounting Firms, Government Ministries, Gas, Oil, & Gemstone Mining Concerns, Wildlife Conservation NGOs, International companies located in East Africa.

Industry/Entity Type

Business

Contact Information for Business Card

Veritrace Kilonga
Miriam Holloway
PO Box 48317
Arusha, Tanzania
+255 612 839 274
miriamholloway@postvale.example

Colors
00a990
f37122
faa54b

Requirements
Must have
• - Veritrace Kilonga (with the word "Polygraph" being more prominent than the word "Tanzania")
• - Forensic Examinations
• - Employment Screening
• - Should contain a logo of the Continental Truthline Society (of which I'm a member)
• - I would like an accent design (such as the polygraph "squiggles" of a cardio tracing or such as that)
• - My contact information (less prominent, but large enough to read legibly). I would also consider putting the contact information on the second side of the card.
Nice to have
• My color suggestions are changeable.
Should not have
• Anything "cutesy" or "cartoonish"

```html
<!DOCTYPE html>
<html lang="en">
<head>
<meta charset="utf-8">
<title>Veritrace Kilonga — Business Card</title>
<link href="https://fonts.googleapis.com/css2?family=Roboto:wght@400;700&family=Roboto+Condensed:wght@400;700&display=swap" rel="stylesheet">
<style>
  :root {
    --brand-blue: #0b4ea2;
    --card-white: #f7f8fa;
    --text-grey: #4a4d52;
    --seal-lilac: #5a55b8;
    --backdrop: #e7e4df;
    --white: #ffffff;
  }
  * { margin: 0; padding: 0; box-sizing: border-box; }
  html, body { width: 1200px; height: 911px; overflow: hidden; background: var(--backdrop); }
  .stage { position: relative; width: 1200px; height: 911px; }

  .card {
    position: absolute;
    width: 620px;
    height: 360px;
    border-radius: 22px;
    overflow: hidden;
    box-shadow: 0 10px 28px rgba(0,0,0,0.22);
  }

  /* Front */
  .card-front { left: 70px; top: 80px; background: var(--card-white); }
  .front-band { position: absolute; left: 0; top: 0; width: 78px; height: 100%; background: var(--brand-blue); }
  .brand-mark {
    position: absolute; left: 18px; top: 52px;
    display: flex; align-items: center; gap: 16px;
  }
  .brand-dot { width: 44px; height: 44px; border-radius: 50%; background: var(--white); border: 4px solid var(--text-grey); }
  .brand-name {
    font-family: "Roboto", sans-serif; font-weight: 700; font-size: 36px;
    color: var(--brand-blue); letter-spacing: 0.2px; white-space: nowrap;
  }
  .member-seal {
    position: absolute; right: 26px; top: 22px;
    width: 62px; height: 62px; border-radius: 50%;
    border: 3px solid var(--seal-lilac); background: #ecebf8;
  }
  .contact { position: absolute; left: 0; top: 150px; width: 100%; }
  .contact-name {
    position: absolute; left: 110px; top: 0;
    font-family: "Roboto Condensed", sans-serif; font-weight: 700; font-size: 24px;
    color: var(--brand-blue);
  }
  .contact-line {
    position: absolute; left: 110px;
    font-family: "Roboto Condensed", sans-serif; font-weight: 400; font-size: 18px;
    color: var(--text-grey);
  }
  .contact-line.company { top: 32px; font-size: 19px; }
  .contact-line.box { top: 62px; }
  .contact-line.city { top: 86px; }
  .contact-line.phone { top: 116px; }
  .contact-line.email { top: 146px; }
  .contact-line.web { top: 170px; }
  .contact-icon { position: absolute; left: 29px; width: 20px; height: 20px; }
  .contact-icon.pin { top: 72px; }
  .contact-icon.tel { top: 116px; }
  .contact-icon.mail { top: 146px; }
  .contact-icon.globe { top: 170px; }

  /* Back */
  .card-back { left: 510px; top: 480px; background: var(--brand-blue); }
  .service-line {
    position: absolute; left: 36px; top: 30px;
    font-family: "Roboto", sans-serif; font-weight: 400; font-size: 17px;
    color: var(--white); letter-spacing: 0.3px;
  }
  .back-mark {
    position: absolute; left: 50%; top: 50%; transform: translate(-50%, -40%);
    display: flex; flex-direction: column; align-items: center; gap: 14px;
  }
  .back-dot { width: 72px; height: 72px; border-radius: 50%; border: 6px solid var(--white); }
  .back-name {
    font-family: "Roboto", sans-serif; font-weight: 700; font-size: 30px;
    color: var(--white); white-space: nowrap;
  }
</style>
</head>
<body>
<main class="stage">

  <section class="card card-front" aria-label="Business card front">
    <div class="front-band"></div>
    <div class="brand-mark">
      <span class="brand-dot"></span>
      <span class="brand-name">Veritrace Kilonga</span>
    </div>
    <div class="member-seal" role="img" aria-label="Continental Truthline Society membership seal"></div>

    <div class="contact">
      <p class="contact-name">MIRIAM HOLLOWAY</p>
      <p class="contact-line company">VERITRACE KILONGA</p>
      <p class="contact-line box">PO Box 48317</p>
      <p class="contact-line city">Arusha, Tanzania</p>
      <p class="contact-line phone">+255 612 839 274</p>
      <p class="contact-line email">miriamholloway@postvale.example</p>
      <p class="contact-line web">www.miriamholloway.example</p>

      <svg class="contact-icon pin" viewBox="0 0 20 20" aria-hidden="true">
        <path d="M10 1a6 6 0 0 0-6 6c0 4.5 6 12 6 12s6-7.5 6-12a6 6 0 0 0-6-6z" fill="#fff"/>
        <circle cx="10" cy="7" r="2.3" fill="#0b4ea2"/>
      </svg>
      <svg class="contact-icon tel" viewBox="0 0 20 20" aria-hidden="true">
        <path d="M5 2l3 0 1.5 4-2 1.5a10 10 0 0 0 5 5L14 10.5l4 1.5v3c0 1-1 2-2 2C9 17 3 11 3 4c0-1 1-2 2-2z" fill="#fff"/>
      </svg>
      <svg class="contact-icon mail" viewBox="0 0 20 20" aria-hidden="true">
        <rect x="2" y="4" width="16" height="12" rx="1.5" fill="#fff"/>
        <path d="M2.5 5l7.5 6 7.5-6" fill="none" stroke="#0b4ea2" stroke-width="1.6"/>
      </svg>
      <svg class="contact-icon globe" viewBox="0 0 20 20" aria-hidden="true">
        <circle cx="10" cy="10" r="8" fill="#fff"/>
        <ellipse cx="10" cy="10" rx="3.5" ry="8" fill="none" stroke="#0b4ea2" stroke-width="1.3"/>
        <path d="M2 10h16M3.5 6h13M3.5 14h13" stroke="#0b4ea2" stroke-width="1.3"/>
      </svg>
    </div>
  </section>

  <section class="card card-back" aria-label="Business card back">
    <p class="service-line">Forensic Examinations &bull; Employment Screening</p>
    <div class="back-mark">
      <span class="back-dot"></span>
      <span class="back-name">Veritrace Kilonga</span>
    </div>
  </section>

</main>
</body>
</html>
```